Psychiatric Office Needs a Website- 1st Time Ever!

Been in practice since 2003 with no website, but finally ready to dive in. We are Maplecrest Behavioral Healthcare, a mental health outpatient practice based in Fayetteville, Georgia that sees diverse individuals and families from childhood to advanced age for a variety of conditions. We've grown by word of mouth and referral but would now like to have a digital footprint. Be the pioneer of our website and we will be sure to share. We would like to see designs that are modern, animated, fairly colorful, easy to read, and caters to all ages. Also, we would like the design to take the whole page (not be centered) and can be viewed well on phone/tablet. Please see our outline for more information. Our motto/slogan is: Maplecrest Behavioral Healthcare- A step forward in your wellness journey, so the design should try to reflect that.
Updates

Project Deadline Extended
Reason: site in progress

Target Market(s)

Children through elderly

Industry/Entity Type

Medical

Logo Text

Stepping forward in your wellness journey

Number of Pages Required

1 page

Colors

Designer to choose colors to be used in the design.

Requirements
Must have
• Animation or moving pictures.
• Color.
• Concise.
• User friendly
• Diversity in the stock photos

```html
<!DOCTYPE html>
<html lang="en">
<head>
<meta charset="utf-8">
<title>Maplecrest Behavioral Healthcare</title>
<link rel="stylesheet" href="https://fonts.googleapis.com/css2?family=Roboto:wght@300;400;500;700&display=swap">
<style>
:root{
  --teal:#2fc7b2;
  --teal-dark:#1fae9c;
  --cyan:#3bbdd2;
  --ink:#2b2b2b;
  --muted:#6f6f6f;
  --light:#f3f3f3;
  --footer:#262626;
  --white:#ffffff;
}
*{margin:0;padding:0;box-sizing:border-box}
html,body{width:1200px;height:3888px;overflow:hidden}
body{font-family:'Roboto',sans-serif;color:var(--ink);background:var(--white);position:relative}
.abs{position:absolute}
.btn{position:absolute;background:var(--cyan);color:var(--white);font-size:17px;font-weight:500;display:flex;align-items:center;justify-content:center;border-radius:4px}

/* header */
.topbar{left:0;top:0;width:1200px;height:91px;background:var(--white)}
.contact-item{top:14px;font-size:16px;color:var(--ink);display:flex;align-items:center;gap:10px}
.contact-icon{width:26px;height:26px;border-radius:50%;background:#e4e4e4;display:flex;align-items:center;justify-content:center}
.portal{left:972px;top:10px;width:206px;height:34px;font-size:15px}
.nav{top:56px;font-size:17px;font-weight:500;color:var(--ink)}
.nav.active{color:var(--teal)}
.logo{left:104px;top:-52px;width:246px;height:246px;border-radius:50%;background:var(--white);box-shadow:0 3px 10px rgba(0,0,0,.18);display:flex;align-items:center;justify-content:center;text-align:center;padding:60px 30px 0;z-index:3}
.logo span{font-size:23px;font-weight:700;color:var(--teal-dark);line-height:1.2}

/* hero */
.hero{left:0;top:91px;width:1200px;height:466px;background:linear-gradient(100deg,#b9a898 0%,#d8cfc6 30%,#c9d6dc 60%,#8aa3b3 100%)}
.hero-title{left:0;top:240px;width:1200px;text-align:center;font-size:48px;font-weight:500;color:var(--white);text-shadow:0 2px 6px rgba(0,0,0,.35)}
.hero-sub{left:0;top:312px;width:1200px;text-align:center;font-size:30px;font-weight:500;color:var(--white);text-shadow:0 2px 6px rgba(0,0,0,.35)}
.hero-btn{left:510px;top:382px;width:180px;height:40px}
.arrow{top:290px;width:30px;height:50px}

/* about */
.about-box{left:100px;top:669px;width:466px;height:290px;border:7px solid var(--cyan);background:var(--white);padding:22px 40px 22px 48px;display:flex;flex-direction:column;align-items:flex-start}
.about-box h2{font-size:30px;font-weight:500;margin-bottom:12px;line-height:1.2}
.about-box p{font-size:13.5px;line-height:1.45;color:var(--muted);margin-bottom:10px}
.about-btn{position:static;margin-top:4px;width:122px;height:38px;flex-shrink:0}
.about-photo{left:604px;top:632px;width:498px;height:366px;background:linear-gradient(135deg,#cbd9e4,#6d8fa8 60%,#33495e);box-shadow:0 2px 8px rgba(0,0,0,.15)}

/* treat */
.treat{left:0;top:1070px;width:1200px;height:654px;background:var(--light)}
.section-title{left:0;width:1200px;text-align:center;font-size:31px;font-weight:700;color:var(--ink)}
.hub{left:451px;top:1208px;width:296px;height:296px;border-radius:50%;background:radial-gradient(circle,#e9f4f6 0%,#9fd3dd 55%,#5bb6c6 100%);border:10px solid #d8ecef}
.t-icon{width:76px;height:76px;border-radius:50%;background:var(--teal);display:flex;align-items:center;justify-content:center}
.t-text{width:280px}
.t-text h3{font-size:19px;font-weight:500;color:var(--cyan);margin-bottom:6px}
.t-text p{font-size:13px;line-height:1.45;color:var(--muted)}
.t-left{text-align:right}

/* doctor band */
.band{left:0;top:1724px;width:1200px;height:448px;background:linear-gradient(90deg,#27b89e,#3cc8b2 60%,#7fd6c8)}
.doctor{left:80px;top:1594px;width:412px;height:578px;background:linear-gradient(180deg,#8a6a55 0%,#b7dbe8 45%,#4a7fb6 100%);border-radius:190px 190px 0 0}
.band-role{left:560px;top:1797px;font-size:30px;font-weight:500;color:var(--white)}
.band-name{left:560px;top:1848px;font-size:38px;font-weight:500;color:var(--white)}
.band-lead{left:560px;top:1912px;width:540px;font-size:19px;font-weight:700;line-height:1.5;color:var(--white)}
.band-body{left:560px;top:1980px;width:540px;font-size:15px;line-height:1.55;color:rgba(255,255,255,.85)}
.band-nav{top:2096px;width:36px;height:36px;border:2px solid var(--white);border-radius:4px;display:flex;align-items:center;justify-content:center}

/* blog */
.card{top:2307px;width:319px;height:290px;background:#fbfbfb;box-shadow:0 2px 6px rgba(0,0,0,.12)}
.card-img{position:absolute;left:0;top:0;width:319px;height:212px}
.card-date{position:absolute;left:0;top:0;width:66px;height:60px;background:var(--cyan);color:var(--white);font-size:14px;font-weight:700;display:flex;flex-direction:column;align-items:center;justify-content:center;line-height:1.3}
.card-body{position:absolute;left:26px;top:166px;width:267px;height:124px;background:var(--white);box-shadow:0 1px 4px rgba(0,0,0,.1);text-align:center;padding-top:20px}
.card-body p{font-size:14px;line-height:1.5;color:var(--ink)}
.card-meta{margin-top:22px;font-size:13px;color:var(--ink);display:flex;justify-content:center;gap:8px}
.card-meta b{font-weight:400;color:var(--teal)}
.view-btn{width:126px;height:40px}

/* faq */
.faq{left:0;top:2755px;width:1200px;height:723px;background:var(--light)}
.faq-item{left:192px;width:816px;background:var(--white);border:1px solid #dedede;box-shadow:0 1px 3px rgba(0,0,0,.06)}
.faq-q{position:absolute;left:36px;top:20px;font-size:16px;font-weight:700;color:var(--ink)}
.faq-a{position:absolute;left:48px;top:76px;width:700px;font-size:14px;line-height:1.6;color:var(--muted)}
.faq-toggle{position:absolute;right:22px;top:16px;width:32px;height:32px;background:var(--cyan);border-radius:3px;color:var(--white);font-size:22px;font-weight:700;display:flex;align-items:center;justify-content:center}
.faq-rule{position:absolute;left:0;top:60px;width:100%;height:1px;background:#e5e5e5}

/* footer */
.footer{left:0;top:3478px;width:1200px;height:410px;background:var(--footer)}
.f-logo{left:148px;top:3504px;width:146px;height:146px;border-radius:50%;background:var(--white);display:flex;align-items:center;justify-content:center;text-align:center;padding:16px}
.f-logo span{font-size:15px;font-weight:700;color:var(--teal-dark);line-height:1.2}
.f-about{left:104px;top:3700px;width:270px;font-size:14px;line-height:1.5;color:var(--white)}
.f-head{top:3540px;font-size:19px;font-weight:700;color:var(--white)}
.f-links{left:504px;top:3583px;list-style:none;font-size:15px;color:var(--white);line-height:28px}
.f-input{left:760px;width:298px;border:1px solid #8a8a8a;color:#bdbdbd;font-size:13px;padding:8px 12px}
.f-submit{left:959px;top:3743px;width:99px;height:36px;font-size:14px;font-weight:700}
.f-rule{left:104px;top:3823px;width:992px;height:1px;background:#555}
.f-copy{left:104px;top:3846px;font-size:14px;color:var(--white)}
.f-social{left:1078px;top:3844px;width:20px;height:20px;background:var(--white);border-radius:3px}
</style>
</head>
<body>

<!-- header -->
<header class="abs topbar">
  <div class="abs contact-item" style="left:648px">
    <span class="contact-icon"><svg width="14" height="14" viewBox="0 0 24 24"><path d="M6.6 10.8a15 15 0 0 0 6.6 6.6l2.2-2.2a1 1 0 0 1 1-.25 11.4 11.4 0 0 0 3.6.57 1 1 0 0 1 1 1V20a1 1 0 0 1-1 1A17 17 0 0 1 3 4a1 1 0 0 1 1-1h3.5a1 1 0 0 1 1 1c0 1.25.2 2.45.57 3.57a1 1 0 0 1-.25 1z" fill="#555"/></svg></span>
    +1 555 014 2273
  </div>
  <div class="abs contact-item" style="left:830px">
    <span class="contact-icon"><svg width="14" height="14" viewBox="0 0 24 24"><circle cx="12" cy="12" r="9" fill="none" stroke="#555" stroke-width="2.4"/><path d="M12 7v5l3 2" fill="none" stroke="#555" stroke-width="2.4"/></svg></span>
    8am - 5pm
  </div>
  <div class="btn portal">Patient Portal</div>
  <span class="abs nav active" style="left:435px">Home</span>
  <span class="abs nav" style="left:516px">About Us</span>
  <span class="abs nav" style="left:617px">Services</span>
  <span class="abs nav" style="left:715px">Conditions We Treat</span>
  <span class="abs nav" style="left:894px">New Patients</span>
  <span class="abs nav" style="left:1026px">Contact Us</span>
</header>
<div class="abs logo"><span>Maplecrest Behavioral Healthcare</span></div>

<!-- hero -->
<section class="abs hero" role="img" aria-label="Photo of a smiling nurse caring for an elderly patient"></section>
<h1 class="abs hero-title">Maplecrest Behavioral Healthcare</h1>
<p class="abs hero-sub">A step forward in your wellness journey</p>
<div class="btn hero-btn">Take A Screening</div>
<svg class="abs arrow" style="left:26px" viewBox="0 0 30 50"><path d="M24 6L8 25l16 19" fill="none" stroke="#fff" stroke-width="4"/></svg>
<svg class="abs arrow" style="left:1144px" viewBox="0 0 30 50"><path d="M6 6l16 19L6 44" fill="none" stroke="#fff" stroke-width="4"/></svg>

<!-- about -->
<section class="abs about-box">
  <h2>About Us</h2>
  <p>To provide mental health services to children, adults, and the developmentally disabled population that is culturally sensitive regardless of age, race, gender, orientation, religion, or creed.</p>
  <p>To work hand in hand with clients to overcome mental health challenges and improve their quality of life.</p>
  <div class="btn about-btn">Read More</div>
</section>
<div class="abs about-photo" role="img" aria-label="Photo of a diverse medical team in a meeting"></div>

<!-- treat -->
<section class="abs treat"></section>
<h2 class="abs section-title" style="top:1140px">We Specially Treat For</h2>
<div class="abs hub" role="img" aria-label="Illustration of a hand touching medical interface icons"></div>

<div class="abs t-text t-left" style="left:98px;top:1222px"><h3>Sleep Issues</h3><p>Lorem Ipsum is simply dummy text of printing and typesetting industry.</p></div>
<div class="abs t-icon" style="left:402px;top:1216px"><svg width="36" height="36" viewBox="0 0 24 24"><path d="M20 14.5A8 8 0 0 1 9.5 4a8 8 0 1 0 10.5 10.5z" fill="#fff"/></svg></div>

<div class="abs t-text t-left" style="left:58px;top:1342px"><h3>Psychotic Disorders</h3><p>Lorem Ipsum is simply dummy text of printing and typesetting industry.</p></div>
<div class="abs t-icon" style="left:364px;top:1333px"><svg width="36" height="36" viewBox="0 0 24 24"><circle cx="12" cy="12" r="8" fill="none" stroke="#fff" stroke-width="2"/><path d="M12 4v16M4 12h16" stroke="#fff" stroke-width="2"/></svg></div>

<div class="abs t-text t-left" style="left:98px;top:1462px"><h3>Eating Disorders</h3><p>Lorem Ipsum is simply dummy text of printing and typesetting industry.</p></div>
<div class="abs t-icon" style="left:402px;top:1458px"><svg width="36" height="36" viewBox="0 0 24 24"><circle cx="12" cy="12" r="6" fill="none" stroke="#fff" stroke-width="2"/><path d="M3 4v16M21 4v16" stroke="#fff" stroke-width="2"/></svg></div>

<div class="abs t-icon" style="left:727px;top:1216px"><svg width="36" height="36" viewBox="0 0 24 24"><path d="M12 20s-7-4.5-7-10a4 4 0 0 1 7-2.6A4 4 0 0 1 19 10c0 5.5-7 10-7 10z" fill="#fff"/></svg></div>
<div class="abs t-text" style="left:827px;top:1222px"><h3>Mood Disorders</h3><p>Lorem Ipsum is simply dummy text of printing and typesetting industry.</p></div>

<div class="abs t-icon" style="left:765px;top:1333px"><svg width="36" height="36" viewBox="0 0 24 24"><path d="M12 3l2.6 5.6 6 .7-4.5 4.1 1.2 6L12 16.4 6.7 19.4l1.2-6L3.4 9.3l6-.7z" fill="#fff"/></svg></div>
<div class="abs t-text" style="left:865px;top:1342px"><h3>Anxiety Disorders</h3><p>Lorem Ipsum is simply dummy text of printing and typesetting industry.</p></div>

<div class="abs t-icon" style="left:727px;top:1458px"><svg width="36" height="36" viewBox="0 0 24 24"><circle cx="12" cy="7" r="3.5" fill="#fff"/><path d="M5 21c0-4.5 3-7.5 7-7.5s7 3 7 7.5z" fill="#fff"/></svg></div>
<div class="abs t-text" style="left:827px;top:1462px"><h3>Childhood Disorders</h3><p>Lorem Ipsum is simply dummy text of printing and typesetting industry.</p></div>

<!-- doctor band -->
<section class="abs band"></section>
<div class="abs doctor" role="img" aria-label="Photo of a smiling psychologist in blue scrubs with a stethoscope"></div>
<p class="abs band-role">Psychologist</p>
<h2 class="abs band-name">DR. Elena Marsh</h2>
<p class="abs band-lead">It is a long established fact that a reader will be readable content of a page when looking at its layout.</p>
<p class="abs band-body">There are many variations of passages of Lorem Ipsum available, but the majority have suffered alteration in some form, by injected humour, or randomised words which don't look even slightly believable.</p>
<div class="abs band-nav" style="left:975px"><svg width="14" height="14" viewBox="0 0 14 14"><path d="M9 2L4 7l5 5" fill="none" stroke="#fff" stroke-width="2"/></svg></div>
<div class="abs band-nav" style="left:1024px"><svg width="14" height="14" viewBox="0 0 14 14"><path d="M5 2l5 5-5 5" fill="none" stroke="#fff" stroke-width="2"/></svg></div>

<!-- blog -->
<h2 class="abs section-title" style="top:2238px">Latest Blog</h2>

<article class="abs card" style="left:98px">
  <div class="card-img" role="img" aria-label="Photo of a doctor with a young girl" style="background:linear-gradient(135deg,#e8ecef,#b9c7d2)"></div>
  <div class="card-date"><span>Sep</span><span>2017</span></div>
  <div class="card-body"><p>Contrary to popular belief,<br>Lorem Ipsum simply random text.</p>
    <div class="card-meta"><span><b>●</b> Owen</span>|<span><b>●</b> 3 Comments</span>|<span><b>♥</b> 12 Likes</span></div></div>
</article>
<article class="abs card" style="left:441px">
  <div class="card-img" role="img" aria-label="Photo of doctors walking through a hospital corridor" style="background:linear-gradient(135deg,#dfe9ef,#8fa9bb)"></div>
  <div class="card-date"><span>Sep</span><span>2017</span></div>
  <div class="card-body"><p>Contrary to popular belief,<br>Lorem Ipsum simply random text.</p>
    <div class="card-meta"><span><b>●</b> Owen</span>|<span><b>●</b> 3 Comments</span>|<span><b>♥</b> 12 Likes</span></div></div>
</article>
<article class="abs card" style="left:780px">
  <div class="card-img" role="img" aria-label="Photo of a hand writing on a medical clipboard" style="background:linear-gradient(135deg,#f3efe9,#cfc3b4)"></div>
  <div class="card-date"><span>Aug</span><span>2017</span></div>
  <div class="card-body"><p>Contrary to popular belief,<br>Lorem Ipsum simply random text.</p>
    <div class="card-meta"><span><b>●</b> Priya</span>|<span><b>●</b> 3 Comments</span>|<span><b>♥</b> 12 Likes</span></div></div>
</article>
<div class="btn view-btn" style="left:537px;top:2641px">View All</div>

<!-- faq -->
<section class="abs faq"></section>
<h2 class="abs section-title" style="top:2822px">FAQ</h2>
<div class="abs faq-item" style="top:2895px;height:158px">
  <p class="faq-q">Contrary to popular belief, Lorem Ipsum is not simply random text ?</p>
  <div class="faq-toggle">−</div>
  <div class="faq-rule"></div>
  <p class="faq-a">There are many variations of passages of Lorem Ipsum available, but the majority have suffered alteration in some form, by injected humour, or randomised words which don't look even slightly believable.</p>
</div>
<div class="abs faq-item" style="top:3084px;height:63px"><p class="faq-q">Contrary to popular belief, Lorem Ipsum is not simply random text ?</p><div class="faq-toggle">+</div></div>
<div class="abs faq-item" style="top:3172px;height:63px"><p class="faq-q">Contrary to popular belief, Lorem Ipsum is not simply random text ?</p><div class="faq-toggle">+</div></div>
<div class="abs faq-item" style="top:3260px;height:63px"><p class="faq-q">Contrary to popular belief, Lorem Ipsum is not simply random text ?</p><div class="faq-toggle">+</div></div>
<div class="btn view-btn" style="left:537px;top:3362px">View All</div>

<!-- footer -->
<footer class="abs footer"></footer>
<div class="abs f-logo"><span>Maplecrest Behavioral Healthcare</span></div>
<p class="abs f-about">There are many variations of passages of Lorem Ipsum available, but the majority have suffered alteration in some form, by injected humour.</p>
<h3 class="abs f-head" style="left:502px">Links</h3>
<ul class="abs f-links">
  <li>Home</li><li>About Us</li><li>Services</li><li>Conditions We Treat</li><li>New Patients</li><li>Contact Us</li>
</ul>
<h3 class="abs f-head" style="left:760px">Contact Form</h3>
<div class="abs f-input" style="top:3590px;height:36px">Email</div>
<div class="abs f-input" style="top:3642px;height:78px">Message</div>
<div class="btn f-submit">SUBMIT</div>
<div class="abs f-rule"></div>
<p class="abs f-copy">Copyright © 2017 Maplecrest Behavioral Healthcare. All Rights Reserved.</p>
<div class="abs f-social"></div>

</body>
</html>
```